Stationery for use with Ninefold Ridge reports

I would like to get a stationery design that my firm -- Ninefold Ridge Advisory -- will use as a format for reports that we send our clients. I am specifically looking for a design for use on a piece of paper or letterhead -- not business cards or envelopes.

We are an Africa based US risk intelligence and strategy firm that works with multinational corporations operating in West Africa. Our initial thinking is that we would like a color scheme consistent with our existing logo -- however we are open to other color schemes.

Also, we would like to see at least two separate versions: one with our company name and logo, the other without name and logo.

We also would like font recommendations for the stationary design.

The final design should communicate discreet professionalism and a modern approach, but it should not overshadow the words and information printed on the stationery.

Target Market(s)

Multinational corporations that currently use our products.

Font styles to use
Serif
Sans Serif

Requirements
Must have
• Sense of discreet professionalism that will not overshadow the content we put onto the stationery format.
• We would like to see designs with and without our company name/logo.
• Please suggest fonts that would work with the stationery.
Nice to have
• Ideally colors consistent with out existing logo, though we are open to and even encourage other ideas.
Should not have
• No need for business cards or envelopes.

```html
<!DOCTYPE html>
<html lang="en">
<head>
<meta charset="utf-8">
<title>Ninefold Ridge Advisory – Letterhead</title>
<link href="https://fonts.googleapis.com/css2?family=Montserrat:wght@700&family=Roboto:wght@300;400&display=swap" rel="stylesheet">
<style>
  :root {
    --backdrop: #d0ebf3;
    --paper: #ffffff;
    --ink-navy: #1f3b4d;
    --ink-grey: #4d5b66;
    --accent-gold: #d99a3c;
    --rule-blue: #a8d3ee;
  }
  * { margin: 0; padding: 0; box-sizing: border-box; }
  html, body {
    width: 1200px; height: 1200px; overflow: hidden;
    background: var(--backdrop);
  }
  .letterhead {
    position: absolute;
    left: 243px; top: 95px;
    width: 715px; height: 1011px;
    background: var(--paper);
    box-shadow: 0 1px 3px rgba(0,0,0,0.25);
  }
  .brand {
    position: absolute;
    left: 40px; top: 36px;
    width: 144px;
    display: flex;
    flex-direction: column;
    align-items: center;
  }
  .brand-mark {
    width: 44px; height: 44px;
    border-radius: 50%;
    background: var(--accent-gold);
  }
  .brand-name {
    margin-top: 12px;
    font-family: "Montserrat", sans-serif;
    font-weight: 700;
    font-size: 17px;
    line-height: 21px;
    text-align: center;
    color: var(--ink-navy);
    white-space: nowrap;
  }
  .contact-list {
    position: absolute;
    left: 421px; top: 72px;
    list-style: none;
    font-family: "Roboto", sans-serif;
    font-weight: 300;
    font-size: 12.5px;
    line-height: 14.5px;
    color: var(--ink-grey);
  }
  .contact-list li { display: flex; align-items: center; gap: 6px; white-space: nowrap; }
  .contact-list svg { width: 9px; height: 9px; fill: var(--accent-gold); flex: none; }
  .contact-list .highlight { color: var(--accent-gold); }
  .contact-divider {
    position: absolute;
    left: 574px; top: 73px;
    width: 1px; height: 40px;
    background: var(--ink-grey);
  }
  .address-block {
    position: absolute;
    left: 592px; top: 72px;
    font-family: "Roboto", sans-serif;
    font-weight: 300;
    font-style: normal;
    font-size: 12.5px;
    line-height: 14.5px;
    color: var(--ink-grey);
  }
  .header-rule {
    position: absolute;
    left: 212px; top: 129px;
    width: 503px; height: 2px;
    background: linear-gradient(to right, rgba(168,211,238,0), var(--rule-blue));
  }
</style>
</head>
<body>
  <main class="letterhead">
    <div class="brand">
      <span class="brand-mark" aria-hidden="true"></span>
      <div class="brand-name">Ninefold Ridge<br>Advisory</div>
    </div>

    <ul class="contact-list">
      <li>
        <svg viewBox="0 0 10 10" aria-hidden="true"><path d="M2 0.5 L3.8 2.6 L2.9 3.8 Q4 6 6.2 7.1 L7.4 6.2 L9.5 8 L8.3 9.5 Q4.5 9.6 0.5 1.7 Z"/></svg>
        <span>555-010-4821</span>
      </li>
      <li>
        <svg viewBox="0 0 10 10" aria-hidden="true"><path d="M0.5 2 H9.5 V8 H0.5 Z M1 2.3 L5 5.5 L9 2.3" stroke="#fff" stroke-width="0.8"/></svg>
        <span>youremail@mail.com</span>
      </li>
      <li>
        <svg viewBox="0 0 10 10" aria-hidden="true"><circle cx="5" cy="5" r="4.5"/><path d="M0.5 5 H9.5 M5 0.5 V9.5" stroke="#fff" stroke-width="0.7"/></svg>
        <span>www.<span class="highlight">yourwebsite</span>.com</span>
      </li>
    </ul>

    <div class="contact-divider"></div>

    <address class="address-block">
      Your address<br>
      city<br>
      state, ZIP 0000
    </address>

    <div class="header-rule"></div>
  </main>
</body>
</html>
```